KORV PTY LTD - Business Cards

Design a modern business card - using the attached Designs.
Same design as on the front, apart from the names/numbers/emails to be different.
We want the cards to be very glossy to stand out, do I think the simple black/white/metallic will be effective.
Both lots of details below:

Tom Wrenshaw
Director
tom_korv@nulvane.com
0438 274 093

Lewis Corbyn
Director
lewis_korv@nulvane.com
0419 385 642

Industry/Entity Type

Business

```html
<!DOCTYPE html>
<html lang="en">
<head>
<meta charset="utf-8">
<title>KORV PTY LTD – Business Cards</title>
<link href="https://fonts.googleapis.com/css2?family=Bitter:wght@400;500&display=swap" rel="stylesheet">
<style>
  :root {
    --page: #e7e4e0;
    --card-white: #ffffff;
    --card-grey: #b5b5b5;
    --charcoal: #30363a;
    --silver: #bfc2c3;
    --ink: #2b2f32;
    --light-text: #ffffff;
  }
  * { margin: 0; padding: 0; box-sizing: border-box; }
  html, body { width: 1200px; height: 475px; overflow: hidden; }
  body {
    background: var(--page);
    font-family: "Bitter", Georgia, serif;
    position: relative;
  }
  .card {
    position: absolute;
    top: 82px;
    width: 540px;
    height: 310px;
    overflow: hidden;
    box-shadow: 0 6px 16px rgba(0,0,0,0.18);
  }
  .card-front { left: 36px; background: var(--card-white); }
  .card-back { left: 624px; background: var(--card-grey); }

  .swoosh { position: absolute; inset: 0; width: 100%; height: 100%; }

  .brand {
    position: absolute;
    display: flex;
    align-items: center;
    gap: 12px;
    color: var(--ink);
    font-weight: 500;
    white-space: nowrap;
  }
  .brand-dot {
    display: block;
    border-radius: 50%;
    background: var(--charcoal);
  }
  .card-front .brand { left: 40px; top: 88px; font-size: 27px; letter-spacing: 1px; }
  .card-front .brand-dot { width: 26px; height: 26px; }
  .card-back .brand {
    left: 50%; top: 50%;
    transform: translate(-50%, -50%);
    font-size: 40px; letter-spacing: 2px;
  }
  .card-back .brand-dot { width: 38px; height: 38px; }

  .person {
    position: absolute;
    right: 40px;
    top: 128px;
    text-align: right;
    color: var(--ink);
  }
  .person-name { font-size: 21px; font-weight: 400; }
  .person-role { font-size: 13px; margin-top: 3px; }

  .contact {
    position: absolute;
    right: 28px;
    top: 222px;
    list-style: none;
    color: var(--light-text);
    font-size: 16px;
    text-align: right;
  }
  .contact li {
    display: flex;
    align-items: center;
    justify-content: flex-end;
    gap: 9px;
    margin-bottom: 12px;
  }
  .contact svg { width: 14px; height: 14px; fill: var(--light-text); }
</style>
</head>
<body>

<section class="card card-front" aria-label="Business card front">
  <svg class="swoosh" viewBox="0 0 540 310" preserveAspectRatio="none" aria-hidden="true">
    <path d="M0 262 C150 300 330 250 540 178 L540 194 C330 262 150 308 0 278 Z" fill="var(--silver)"/>
    <path d="M0 272 C160 306 340 262 540 192 L540 310 L0 310 Z" fill="var(--charcoal)"/>
  </svg>

  <div class="brand"><span class="brand-dot"></span>KORV PTY LTD</div>

  <div class="person">
    <div class="person-name">Lewis Corbyn</div>
    <div class="person-role">Director</div>
  </div>

  <ul class="contact">
    <li>
      <svg viewBox="0 0 24 24" aria-hidden="true"><path d="M6.6 10.8a15.1 15.1 0 0 0 6.6 6.6l2.2-2.2a1 1 0 0 1 1-.25 11.4 11.4 0 0 0 3.6.57 1 1 0 0 1 1 1V20a1 1 0 0 1-1 1A17 17 0 0 1 3 4a1 1 0 0 1 1-1h3.5a1 1 0 0 1 1 1c0 1.25.2 2.45.57 3.57a1 1 0 0 1-.25 1z"/></svg>
      0419 385 642
    </li>
    <li>
      <svg viewBox="0 0 24 24" aria-hidden="true"><path d="M2 6h20v12H2z M2 6l10 7 10-7" fill="none" stroke="#fff" stroke-width="2"/></svg>
      lewis_korv@nulvane.com
    </li>
  </ul>
</section>

<section class="card card-back" aria-label="Business card back">
  <div class="brand"><span class="brand-dot"></span>KORV PTY LTD</div>
</section>

</body>
</html>
```